New web page, 2 companies on the one page

A new web page for an engineering consultancy and maintenance management company

Corlett & Associates is the parent company covering the design and consultancy
Valtrix Engineering is the Maintenance and Reliability company

Target Market(s)

Food & Beverage, ingredients Manufacturing
engineering managers

Coding

Coded - Design and coding required

Number of Pages Required

1 page

Font styles to use
Other font styles liked:
• Roboto

Colors
1861ab
85acd3
d0dfed
cee9f5

```html
<!DOCTYPE html>
<html lang="en">
<head>
<meta charset="utf-8">
<title>Corlett &amp; Associates</title>
<link href="https://fonts.googleapis.com/css2?family=Roboto:wght@400;500;700&family=Lato:wght@400;700&display=swap" rel="stylesheet">
<style>
:root{
  --navy:#1861ab;
  --sky:#85acd3;
  --mist:#d0dfed;
  --ice:#cee9f5;
  --ink:#111a22;
  --text:#333;
  --white:#fff;
  --black:#000;
}
*{margin:0;padding:0;box-sizing:border-box}
html,body{width:1200px;height:3114px;overflow:hidden;background:var(--white)}
body{position:relative;font-family:'Lato',sans-serif;color:var(--text)}
.abs{position:absolute}
.topbar{left:0;top:0;width:1200px;height:44px;background:var(--sky);color:var(--white);font-family:'Roboto',sans-serif;font-size:15px}
.topbar .contact{position:absolute;left:111px;top:13px;display:flex;gap:30px;align-items:center}
.topbar .item{display:flex;align-items:center;gap:8px}
.topbar .right{position:absolute;right:112px;top:13px;display:flex;gap:18px;align-items:center}
.dot-icon{width:11px;height:11px;border-radius:50%;background:var(--white);display:inline-block}
.header{left:0;top:44px;width:1200px;height:86px;background:var(--white);box-shadow:0 2px 4px rgba(0,0,0,.08)}
.brand{position:absolute;left:117px;top:28px;display:flex;align-items:center;gap:8px;font-family:'Roboto',sans-serif;font-weight:700;font-size:19px;color:var(--navy)}
.brand i{width:22px;height:22px;background:var(--navy);border-radius:50%;display:block}
.nav{position:absolute;top:34px;font-family:'Roboto',sans-serif;font-size:16px;color:var(--ink);letter-spacing:.3px}
.nav.active::after{content:"";position:absolute;left:0;right:0;top:24px;height:2px;background:var(--sky)}
.search{position:absolute;left:1075px;top:38px}
.hero{left:0;top:130px;width:1200px;height:680px}
.hero-title{left:0;top:352px;width:1200px;text-align:center;font-family:'Roboto',sans-serif;font-weight:700;font-size:48px;color:var(--white);letter-spacing:2px}
.hero-sub{left:300px;top:425px;width:600px;text-align:center;font-size:16px;line-height:23px;color:var(--white)}
.btn{display:flex;align-items:center;justify-content:center;background:var(--sky);color:var(--white);font-family:'Roboto',sans-serif;font-weight:700;font-size:17px;letter-spacing:.8px}
.hero-btn{left:522px;top:499px;width:155px;height:42px}
.chev{font-family:'Roboto',sans-serif;color:var(--white);font-size:28px}
.section-title{left:0;width:1200px;text-align:center;font-family:'Roboto',sans-serif;font-weight:700;font-size:38px;color:var(--ink);letter-spacing:1px}
.underline{height:3px;background:var(--sky)}
.card{top:980px;width:306px;height:410px;background:var(--white);box-shadow:0 0 10px rgba(0,0,0,.12);border-bottom:3px solid var(--sky);text-align:center}
.card .photo{width:306px;height:186px}
.card h3{margin-top:24px;font-family:'Roboto',sans-serif;font-weight:500;font-size:15px;color:var(--sky)}
.card .rule{width:28px;height:1px;background:#999;margin:12px auto 14px}
.card p{font-size:15.5px;line-height:24px;padding:0 28px;color:#333}
.card .more{margin-top:14px;font-size:15.5px;color:var(--sky);display:flex;justify-content:center;align-items:center;gap:8px}
.card .more i{width:13px;height:13px;border-radius:50%;background:var(--sky);display:inline-block}
.carousel-arrow{width:22px;height:22px;border-radius:50%;background:var(--navy);opacity:.8}
.about{left:0;top:1468px;width:1200px;height:593px;background:linear-gradient(180deg,#e6eef6 0%,#dfe9f3 50%,#d6e3ef 100%)}
.about-title{left:129px;top:1645px;font-family:'Roboto',sans-serif;font-weight:700;font-size:38px;color:var(--ink)}
.about-text{left:129px;top:1731px;width:510px;font-size:15.5px;line-height:27.5px;color:#222}
.about-btn{left:129px;top:1901px;width:155px;height:42px}
.about-mark{left:773px;top:1740px;width:300px;display:flex;align-items:center;gap:14px;font-family:'Roboto',sans-serif;font-weight:700;font-size:30px;color:var(--navy)}
.about-mark i{width:46px;height:46px;border-radius:50%;background:var(--navy);flex:none}
.avatar{left:555px;top:2255px;width:88px;height:88px;border-radius:50%;background:linear-gradient(160deg,#c9ccd1,#6d737c);box-shadow:0 3px 8px rgba(0,0,0,.25)}
.tname{left:0;top:2368px;width:1200px;text-align:center;font-family:'Roboto',sans-serif;font-weight:500;font-size:16px;color:var(--ink)}
.quote{left:0;top:2400px;width:1200px;text-align:center;font-family:'Roboto',sans-serif;font-weight:700;font-size:54px;line-height:54px;color:var(--sky)}
.ttext{left:230px;top:2462px;width:740px;text-align:center;font-size:15px;line-height:26px;color:#333}
.pager{width:10px;height:10px;border-radius:50%;top:2603px;background:var(--ink)}
.footer{left:0;top:2690px;width:1200px;height:424px}
.foot-brand{left:0;top:2788px;width:1200px;display:flex;justify-content:center;align-items:center;gap:12px;font-family:'Roboto',sans-serif;font-weight:700;font-size:26px;color:var(--white)}
.foot-brand i{width:30px;height:30px;border-radius:50%;background:var(--sky);display:block}
.fnav{top:2877px;font-family:'Roboto',sans-serif;font-weight:500;font-size:16px;color:var(--white);letter-spacing:.5px}
.social{top:2945px;width:38px;height:38px;border-radius:50%;background:var(--sky)}
.fline{left:111px;top:3032px;width:977px;height:1px;background:#555}
.copy{left:0;top:3058px;width:1200px;text-align:center;font-family:'Roboto',sans-serif;font-weight:500;font-size:15px;color:var(--white)}
</style>
</head>
<body>

<div class="abs topbar">
  <div class="contact">
    <span class="item"><svg width="12" height="12" viewBox="0 0 12 12"><path d="M2 1l2 0 1 3-1.5 1a7 7 0 003.5 3.5l1-1.5 3 1 0 2a1 1 0 01-1 1A9 9 0 011 2a1 1 0 011-1z" fill="#fff"/></svg>(123) 456 789</span>
    <span class="item"><svg width="14" height="11" viewBox="0 0 14 11"><rect x="1" y="1" width="12" height="9" fill="none" stroke="#fff" stroke-width="1.4"/><path d="M1 1l6 5 6-5" fill="none" stroke="#fff" stroke-width="1.4"/></svg>info@corlettassociates.com</span>
  </div>
  <div class="right">
    <span class="item"><svg width="13" height="12" viewBox="0 0 13 12"><path d="M1 6h7M5 3l3 3-3 3" fill="none" stroke="#fff" stroke-width="1.6"/><path d="M8 1h4v10H8" fill="none" stroke="#fff" stroke-width="1.4"/></svg>Login</span>
    <span class="dot-icon" style="margin-left:14px"></span><span class="dot-icon"></span><span class="dot-icon"></span><span class="dot-icon"></span>
  </div>
</div>

<div class="abs header">
  <div class="brand"><i></i>Corlett &amp; Associates</div>
  <span class="nav active" style="left:358px">HOME</span>
  <span class="nav" style="left:465px">ABOUT US</span>
  <span class="nav" style="left:603px">SERVICES</span>
  <span class="nav" style="left:738px">TESTIMONIAL</span>
  <span class="nav" style="left:904px">CONTACT US</span>
  <svg class="search" width="14" height="14" viewBox="0 0 14 14"><circle cx="6" cy="6" r="4.3" fill="none" stroke="#111" stroke-width="2"/><path d="M9 9l4 4" stroke="#111" stroke-width="2.2"/></svg>
</div>

<svg class="abs hero" viewBox="0 0 1200 680" role="img" aria-label="Harbour city skyline with bridge and boats at sunset">
  <defs>
    <linearGradient id="sky" x1="0" y1="0" x2="0" y2="1">
      <stop offset="0" stop-color="#b7a58f"/>
      <stop offset=".35" stop-color="#8d8a86"/>
      <stop offset=".55" stop-color="#5f7184"/>
      <stop offset="1" stop-color="#3f5f7d"/>
    </linearGradient>
  </defs>
  <polygon points="0,0 1200,0 1200,553 600,645 0,553" fill="url(#sky)"/>
  <polygon points="0,553 600,645 1200,553 1200,570 600,662 0,570" fill="#85acd3"/>
</svg>
<div class="abs chev" style="left:48px;top:433px">&#8249;</div>
<div class="abs chev" style="left:1136px;top:433px">&#8250;</div>
<div class="abs hero-title">CORLETT ASSOCIATES</div>
<div class="abs hero-sub">Corlett &amp; Associates is specialised manufacturing engineering support organisation that can provide fast, nimble, and flexible services.</div>
<div class="abs btn hero-btn">GET STARTED</div>

<div class="abs section-title" style="top:860px">OUR SERVICES</div>
<div class="abs underline" style="left:556px;top:920px;width:87px"></div>

<div class="abs carousel-arrow" style="left:37px;top:1173px"></div>
<div class="abs carousel-arrow" style="left:1139px;top:1173px"></div>

<div class="abs card" style="left:111px">
  <div class="photo" role="img" aria-label="Team meeting around a laptop" style="background:linear-gradient(135deg,#5a6470,#b9a58e 60%,#d8d2c8)"></div>
  <h3>Project Management</h3><div class="rule"></div>
  <p>Lorem ipsum dolor sit amet, consectetur adipiscing elit, sed do eiusmod tempor incididunt ut labore et dolore magna aliqua.</p>
  <div class="more">Read More <i></i></div>
</div>
<div class="abs card" style="left:447px">
  <div class="photo" role="img" aria-label="Engineers reviewing plans with hard hat on table" style="background:linear-gradient(135deg,#7a8590,#c9c2b2 55%,#e6d27a)"></div>
  <h3>Maintenance Execution</h3><div class="rule"></div>
  <p>Lorem ipsum dolor sit amet, consectetur adipiscing elit, sed do eiusmod tempor incididunt ut labore et dolore magna aliqua.</p>
  <div class="more">Read More <i></i></div>
</div>
<div class="abs card" style="left:782px">
  <div class="photo" role="img" aria-label="Engineers studying drawings on a workbench" style="background:linear-gradient(135deg,#4c4a4a,#9b8f82 55%,#ddd8cf)"></div>
  <h3>Process &amp; Facilities Design</h3><div class="rule"></div>
  <p>Lorem ipsum dolor sit amet, consectetur adipiscing elit, sed do eiusmod tempor incididunt ut labore et dolore magna aliqua.</p>
  <div class="more">Read More <i></i></div>
</div>

<div class="abs about" role="img" aria-label="Faint city skyline background"></div>
<svg class="abs" style="left:0;top:1466px" width="1200" height="130" viewBox="0 0 1200 130">
  <polygon points="0,0 1200,0 1200,8 0,6" fill="#fff"/>
  <polygon points="0,6 580,78 0,44" fill="#cee9f5"/>
  <polygon points="580,78 1200,8 1200,124" fill="#85acd3"/>
</svg>
<div class="abs about-title">ABOUT US</div>
<div class="abs underline" style="left:129px;top:1705px;width:86px"></div>
<div class="abs about-text">Corlett &amp; Associates is specialised manufacturing engineering support organisation that can provide fast, nimble, and flexible services. We have a proven track record in delivering tangible outcomes in process design and fit-out, project management, manufacturing process and maintenance design and execution.</div>
<div class="abs btn about-btn">LEARN MORE</div>
<div class="abs about-mark"><i></i>Corlett &amp; Associates</div>

<div class="abs section-title" style="top:2138px">CLIENT TESTIMONIALS</div>
<div class="abs underline" style="left:556px;top:2206px;width:87px"></div>
<div class="abs avatar" role="img" aria-label="Client portrait"></div>
<div class="abs tname">Jhon Deo</div>
<div class="abs quote">&#8220;</div>
<div class="abs ttext">Lorem ipsum dolor sit amet, consectetur adipiscing elit, sed do eiusmod tempor incididunt ut labore et dolore magna aliqua. Ut enim ad minim veniam, quis nostrud exercitation ullamco laboris nisi ut aliquip ex ea commodo consequat. Duis aute irure dolor in reprehenderit in voluptate velit esse cillum dolore eu fugiat nulla pariatur. Excepteur sint occaecat cupidatat non proident, sunt in culpa quium.</div>
<div class="abs pager" style="left:569px;background:var(--sky)"></div>
<div class="abs pager" style="left:595px"></div>
<div class="abs pager" style="left:621px"></div>

<svg class="abs footer" viewBox="0 0 1200 424">
  <polygon points="0,116 600,11 1200,116 1200,424 0,424" fill="#85acd3"/>
  <polygon points="0,124 600,28 1200,124 1200,424 0,424" fill="#000"/>
</svg>
<div class="abs foot-brand"><i></i>Valtrix Engineering</div>
<span class="abs fnav" style="left:308px">HOME</span>
<span class="abs fnav" style="left:415px">ABOUT US</span>
<span class="abs fnav" style="left:553px">SERVICES</span>
<span class="abs fnav" style="left:688px">TEAM</span>
<span class="abs fnav" style="left:792px">CONTACT US</span>
<div class="abs social" style="left:504px" aria-label="Social link"></div>
<div class="abs social" style="left:556px" aria-label="Social link"></div>
<div class="abs social" style="left:607px" aria-label="Social link"></div>
<div class="abs social" style="left:659px" aria-label="Social link"></div>
<div class="abs fline"></div>
<div class="abs copy">&copy;Copyright@2021Corlett Associates.All right reserved.</div>

</body>
</html>
```